Business Card Design Project

We need a business card design for a company based in San Diego California named "TKLMasonry Inc." We are dedicated installers of fireplaces, pre cast concrete, stone masonry. We also pecialice in block construction.
Updates

Thank you very much guys, very good designs so far although I would like to point out that the front should have: Company name, license number, and please tell me if a Qr code is too much (if it isn't then it should be in a bottom corner. <img src="http://qr.pontebo-demo.com/?l=1&s=8&d=BEGIN:VCARD%0AVERSION:2.1%0AN:Elizondo;Tomas+%0AFN:Tomas++Elizondo%0ATEL;WORK;VOICE:19495550134%0AEMAIL;WORK;INTERNET:tklmasonry%40mailbox-demo.com%0AURL:www.tklmasonry-demo.com%0AORG:TKL+Masonry+Inc%0ATITLE:Contractor%0AADR;WORK:;;;Oceanside;California;91734;USA%0AEND:VCARD" alt="QRCode"/>  Or I'll upload the picture.

Also we are currently constructing our website, there you can find pictures of what we do. 
tklmasonry-demo.com 
Thank you guys again.

Industry/Entity Type

Business

Requirements
Must have
• Company name: T K L Masonry Inc
Licence number: 482915
Tomas Elizondo Vega
Phone number: 8410 555 0199
Nice to have
• We would like to have an image that represents the business area of work; a fireplace, a fountain, a balcony, a niche, an arch.

```html
<!DOCTYPE html>
<html lang="en">
<head>
<meta charset="utf-8">
<title>T K L Masonry Inc. — Business Card</title>
<link rel="stylesheet" href="https://fonts.googleapis.com/css2?family=Open+Sans:wght@300;400&display=swap">
<style>
  :root {
    --page-bg: #ffffff;
    --card-bg: #232323;
    --ink: #ffffff;
  }
  * { margin: 0; padding: 0; box-sizing: border-box; }
  html, body {
    width: 1200px;
    height: 900px;
    overflow: hidden;
    background: var(--page-bg);
  }
  .canvas {
    position: relative;
    width: 1200px;
    height: 900px;
  }
  .card {
    position: absolute;
    left: 113px;
    top: 149px;
    width: 1003px;
    height: 600px;
    background: var(--card-bg);
  }
  .card-frame {
    position: absolute;
    left: 0;
    top: 0;
    width: 1003px;
    height: 600px;
  }
  .brand {
    position: absolute;
    left: 0;
    width: 1003px;
    text-align: center;
    color: var(--ink);
    font-family: "Open Sans", Arial, sans-serif;
    white-space: nowrap;
  }
  .brand-name {
    top: 256px;
    font-size: 45px;
    font-weight: 400;
    letter-spacing: 3.5px;
    word-spacing: -4px;
    line-height: 56px;
    padding-left: 3px;
  }
  .brand-initials {
    letter-spacing: 7px;
  }
  .brand-web {
    top: 314px;
    font-size: 19px;
    font-weight: 400;
    letter-spacing: 1.1px;
    line-height: 26px;
  }
</style>
</head>
<body>
  <div class="canvas">
    <section class="card">
      <svg class="card-frame" viewBox="0 0 1003 600" aria-hidden="true">
        <polyline points="223,193 223,406 435,406" fill="none" stroke="#ffffff" stroke-width="3"/>
        <polyline points="569,195 780,195 780,408" fill="none" stroke="#ffffff" stroke-width="3"/>
      </svg>
      <h1 class="brand brand-name"><span class="brand-initials">TKL</span> MASONRY INC.</h1>
      <p class="brand brand-web">www.tklmasonry-demo.com</p>
    </section>
  </div>
</body>
</html>
```